2-Page Flyer for the Information Session about the Quiet Pathfinder Course

This is a flyer to announce/advertise an evening Information Session about the Quiet Pathfinder Course. This Program aims at mindfully rethinking and redesigning work (and life) for people who feel stuck or not entirely satisfied with their work and/or life (please see draft flyer attached for more details). This Program is property of Bright Meadow, a company that uses a combination of Mindfulness, Design, and Entrepreneurship to help people achieve greater happiness (in their work and lives).

Target Market(s)

People who feel stuck or not entirely satisfied with their work and/or life (please see draft flyer attached for more details)

Font styles to use
Serif
Sans Serif

Colors
ffffff
f37122
33a6d7
acd037

Requirements
Must have
• All of what I will say below is suggestive (I’m not a design expert), and I’m open to divert from it, if it makes sense and feels more interesting.
• I thought initially of a 2-page flyer (please see draft flyer attached). The first page could help people grasp the essence of the event quickly (in 1 or 2 minutes), and then, if they are interested/motivated, they would continue reading through page 2, which has more info about the Program in itself.
• Potential Structure
• Page 1
• . About the Information Session on the Quiet Pathfinder Course
• . Visible Date & Time, Contacts, Venue (and other relevant info)
• . About me (the facilitator)
• Page 2
• . About the Quiet Pathfinder Course
• I include a Powerpoint draft of the flyer with the content. The design is rudimentary and precarious from an aesthetics/organization point of view, and this is mainly where I need help (and maybe in other aspects too!).
• On the flyer, I would like to include:
• . A photo of myself (I attach 1 picture).
• . 1 or 2 beautiful-nature photos (cropped or full). One may have to do with looking at the sky, dreaming, and imagining a new work and life (2 photos with sky and clouds attached). The other has to do with walking the transformation journey (the photo with the person walking through the forest path).
• . bright meadow logo or logos (there are two slightly different ones, that can be used for different purposes). For the first page, I would like the bright meadow logo that has "bright meadow" written on the bottom, with the saying "Stillness, Craft and Venture for Bright Meadow" beneath. This is the main logo. For the 2nd page, you can choose the logo that adapts better.
• - Where it says the "the way out is in" it would be great to have a similar font to the one I attach (see file "Font_the_way_out_is_in.png" and Ankecallig-fg.ttf
Nice to have
• In terms of colours, I would not divert much from the logo colours (and of course white and black). I would like the flyer to be quite white. Almost like fairy-tale white: the white horse, the white snow, the white of the stars, the white heaven. White could be the base colour. White means peace, tranquillity, calm contentment, a smile.
• And then use the other colours. The green of the mindfulness. The blue of the sky, the dreams. And the orange of the sun, the energy, the fire, the action. And maybe the black for text.
• Where it says the "the way out is in" it would be great to have a similar font to the one I attach (see file "Font_the_way_out_is_in".
• I would like this flyer to be a piece of art, in every possible way. Simple, beautiful, ease, light, peaceful, calm happy. Just like the Quiet Pathfinder Course and bright meadow Company that I am creating intends to be. The mission of this Program and Company is to be a designer, a painter (a Picasso) of happier and more fulfilling human lives.
• I am very much looking forward to seeing your proposal(s).

```html
<!DOCTYPE html>
<html lang="en">
<head>
<meta charset="utf-8">
<title>Quiet Pathfinder Course – Information Session Flyer</title>
<link rel="stylesheet" href="https://fonts.googleapis.com/css2?family=Lato:wght@300;400;700;900&family=Oswald:wght@500&family=Crimson+Text:wght@400&display=swap">
<style>
:root{
  --orange:#f37122;
  --blue:#33a6d7;
  --green:#acd037;
  --green-deep:#8dc63f;
  --white:#ffffff;
  --ink:#1b1b1b;
  --ink-green:#1f4a1a;
  --stage:#303030;
  --sky-1:#eaf3f9;
  --grey-circle:#bdbdbd;
}
*{margin:0;padding:0;box-sizing:border-box}
html,body{width:1200px;height:900px;overflow:hidden;background:var(--stage)}
body{position:relative;font-family:"Lato",Arial,sans-serif;color:var(--ink)}
.page{position:absolute;top:66px;width:516px;height:730px;background:var(--white);overflow:hidden;box-shadow:0 4px 14px rgba(0,0,0,.45)}
.page-front{left:81px}
.page-back{left:632px}
.abs{position:absolute}

/* front page */
.sky-photo{position:absolute;inset:0;background:linear-gradient(180deg,var(--sky-1) 0%,#f7fafc 35%,#dfeaf1 70%,#f4f4f4 100%)}
.figure-photo{position:absolute;left:300px;top:0;width:216px;height:660px;background:radial-gradient(ellipse at 55% 45%,rgba(255,255,255,.95) 0%,rgba(240,236,232,.8) 40%,rgba(200,214,224,0) 75%)}
.brand{left:28px;top:46px;display:flex;align-items:center;gap:12px}
.brand-dot{width:50px;height:50px;border-radius:50%;background:var(--blue)}
.brand-name{font-weight:300;font-size:25px;line-height:24px;color:var(--blue)}
.title-main{left:28px;top:132px;font-weight:900;font-size:62px;line-height:62px;color:var(--orange);letter-spacing:1px}
.title-sub{left:28px;top:194px;font-weight:700;font-size:23px;color:var(--ink)}
.band{position:absolute;color:var(--white);font-weight:700;padding-left:28px}
.band-date{top:226px;left:0;width:380px;height:26px;font-size:16px;line-height:26px;font-weight:400;background:linear-gradient(90deg,var(--green) 65%,rgba(172,208,55,0))}
.venue{left:28px;top:257px;font-size:14.5px;font-weight:700}
.band-info{top:302px;left:0;width:300px;height:22px;font-size:15px;line-height:22px;padding-left:33px;background:linear-gradient(90deg,var(--blue) 60%,rgba(51,166,215,0))}
.band-cost{top:373px;left:0;width:330px;height:22px;font-size:15px;line-height:22px;background:linear-gradient(90deg,var(--orange) 60%,rgba(243,113,34,0))}
.band-host{top:446px;left:0;width:230px;height:22px;font-size:15px;line-height:22px;background:linear-gradient(90deg,var(--green) 55%,rgba(172,208,55,0))}
.note{left:28px;width:330px;font-size:8.6px;line-height:11.5px;font-weight:700;color:var(--ink-green)}
.host-name{left:0;width:516px;top:477px;text-align:center;font-size:12.5px;font-weight:700}
.portrait-ring{left:32px;top:502px;width:132px;height:132px;border-radius:50%;border:2px solid var(--orange);padding:5px;background:var(--white)}
.portrait{width:100%;height:100%;border-radius:50%;background:linear-gradient(160deg,#d9d9d9,#8c8f93 70%,#4a5058)}
.bio{left:177px;top:503px;width:210px;font-size:8.6px;line-height:10.5px;text-align:justify}
.web{left:22px;top:674px;font-size:9.5px;letter-spacing:1.6px;color:#333}
.foot-shape{left:0;top:660px;width:516px;height:70px}
.tel{left:282px;top:670px;font-family:"Oswald",Arial,sans-serif;font-weight:500;font-size:19px;color:var(--white)}
.tel-note{left:282px;top:694px;width:200px;font-size:9.5px;line-height:11px;color:var(--white)}

/* back page */
.back-title{left:0;width:516px;text-align:center;top:40px;font-weight:900;font-size:39px;line-height:40px;color:var(--green-deep)}
.back-sub{left:0;width:516px;text-align:center;top:78px;font-weight:400;font-size:36px;line-height:38px}
.lead{left:25px;top:130px;width:476px;font-size:8.9px;line-height:11.2px;text-align:justify}
.band-what{top:173px;left:0;width:340px;height:24px;font-size:15px;line-height:24px;background:linear-gradient(90deg,var(--orange) 65%,rgba(243,113,34,0))}
.band-prog{top:337px;left:0;width:225px;height:25px;font-size:15px;line-height:25px;padding-left:38px;background:linear-gradient(90deg,var(--blue) 60%,rgba(51,166,215,0))}
.band-why{top:454px;left:228px;width:288px;height:25px;font-size:15px;line-height:25px;padding-left:126px;background:linear-gradient(270deg,var(--orange) 65%,rgba(243,113,34,0))}
.cycle{left:70px;top:205px;width:190px;height:130px}
.about{left:255px;top:212px;width:238px;font-size:8.9px;line-height:11.2px;text-align:justify}
.prog-text{left:25px;top:372px;width:222px;font-size:8.9px;line-height:11.2px;text-align:justify}
.ticks{left:268px;top:372px;width:230px;list-style:none;font-size:8.9px;line-height:11.2px}
.ticks li,.why-list li{display:flex;gap:7px;margin-bottom:5px}
.tick{flex:none;width:10px;height:10px;margin-top:1px}
.walk-photo{left:0;top:479px;width:516px;height:160px;background:linear-gradient(180deg,rgba(255,255,255,1) 0%,#eeeeee 45%,#e4e4e4 75%,#f4f4f4 100%)}
.why-head{left:0;width:516px;text-align:center;top:494px;font-size:9.5px;font-weight:700}
.why-list{list-style:none;font-size:8.9px;line-height:11.2px;width:205px}
.why-left{left:30px;top:520px}
.why-right{left:270px;top:520px}
.why-list li{margin-bottom:13px}
.divider{left:264px;top:520px;width:1px;height:56px;background:#9a9a9a}
.format{left:30px;width:456px;top:600px;text-align:center;font-size:9.5px;line-height:13px;font-weight:700}
.band-way{left:0;top:642px;width:516px;height:37px;background:var(--green);text-align:center;font-family:"Crimson Text",Georgia,serif;font-size:19px;line-height:37px;color:#163016;letter-spacing:.4px}
.contact{top:692px;font-size:7.8px;line-height:10px;font-weight:700}
.contact-left{left:48px}
.contact-right{left:305px;text-align:right;width:180px}
</style>
</head>
<body>

<section class="page page-front">
  <div class="sky-photo" role="img" aria-label="Soft photo of a bright sky with light clouds over the sea"></div>
  <div class="figure-photo" role="img" aria-label="Photo of a woman in a white dress seen from behind, arms raised to the sky"></div>

  <div class="abs brand"><span class="brand-dot"></span><span class="brand-name">bright<br>meadow</span></div>

  <h1 class="abs title-main">QUIET</h1>
  <p class="abs title-sub">Pathfinder Course</p>

  <p class="band band-date">Thursday 18th July 2019, from 19:30 to 21:00</p>
  <p class="abs venue">Venue: Lumen Coworking, C/ Olivar 42, Valmora</p>

  <h2 class="band band-info">Information Session</h2>
  <p class="abs note" style="top:331px">The purpose of this Information Session is to give you a real insight into the Quiet Pathfinder Course and how it can help you get the most out of your work and life.</p>

  <h2 class="band band-cost">How much and who can come?</h2>
  <p class="abs note" style="top:405px">The purpose of this Information Session is to give you a real insight into the Quiet Pathfinder Course and how it can help you get the most out of your work and life.</p>

  <h2 class="band band-host">Facilitator</h2>
  <p class="abs host-name">Dr Tomas Arvelo, Visiting Research Fellow, Westbrook University</p>

  <div class="abs portrait-ring"><div class="portrait" role="img" aria-label="Portrait photo of the facilitator"></div></div>
  <p class="abs bio">Tomas joined Westbrook University (School of Management) as a Lecturer in Entrepreneurship in 2015. He completed his PhD in Entrepreneurship at Northfield Business School (Northfield University) in 2014. His dissertation received the Calder Doctoral Dissertation Award from the Society of Management Studies. Tomas began his working career in the semiconductor industry as a production engineer (Corvane), and then in health-care as a sales engineer (Heliant). After his MBA, he worked as a strategy consultant at Riverstone Business School. Originally from Portugal, Tomas enjoys designing and launching new ideas, international communities, mindfulness retreats, and musical improvisation.</p>

  <svg class="abs foot-shape" viewBox="0 0 516 70" aria-hidden="true">
    <path d="M0 40 H216 Q222 40 226 30 L232 8 Q236 0 246 0 H516 V70 H0 Z" fill="var(--orange)"/>
  </svg>
  <p class="abs web">www.tomasarvelo.net</p>
  <p class="abs tel">Tel: +34 611 402 735</p>
  <p class="abs tel-note">Information &amp; Booking: Please contact for more information or to book a place</p>
</section>

<section class="page page-back">
  <h1 class="abs back-title">WHAT IS QUIET</h1>
  <p class="abs back-sub">Pathfinding</p>
  <p class="abs lead">Being mindful means being aware and awake. Entrepreneurship is the creation of a new form of organising. Quiet Pathfinding is then the process of creating or redesigning your work and life with awareness, in a way that is reflective of you, of your passions and values, thus conducing to a greater sense of fulfilment and happiness.</p>

  <h2 class="band band-what">What is Quiet Pathfinding</h2>

  <svg class="abs cycle" viewBox="0 0 190 130" aria-label="Cycle of four workshops joined by weekly peer support meetings" font-family="Lato,Arial,sans-serif">
    <g fill="none" stroke="#9a9a9a" stroke-width="1.2">
      <path d="M112 24 Q128 30 132 46"/><path d="M132 84 Q128 100 112 106"/><path d="M70 106 Q54 100 50 84"/><path d="M50 46 Q54 30 70 24"/>
    </g>
    <circle cx="91" cy="24" r="22" fill="var(--green)"/>
    <circle cx="136" cy="65" r="22" fill="var(--blue)"/>
    <circle cx="91" cy="106" r="22" fill="var(--orange)"/>
    <circle cx="46" cy="65" r="22" fill="var(--grey-circle)"/>
    <g fill="#fff" font-size="4.6" font-weight="700" text-anchor="middle">
      <text x="91" y="20">Workshop 1</text><text x="91" y="26">-INSIGHT-</text><text x="91" y="32">(5 hours)</text>
      <text x="136" y="61">Workshop 2</text><text x="136" y="67">-DESIGN-</text><text x="136" y="73">(5 hours)</text>
      <text x="91" y="102">Workshop 3</text><text x="91" y="108">-EXECUTE-</text><text x="91" y="114">(5 hours)</text>
      <text x="46" y="61">Workshop 4</text><text x="46" y="67">-PRESENT-</text><text x="46" y="73">(5 hours)</text>
    </g>
    <g fill="#444" font-size="4.4">
      <text x="118" y="20">Weekly Peer Support</text><text x="118" y="25">(WPS) meetings</text>
      <text x="22" y="30">WPS meetings</text><text x="140" y="100">WPS meetings</text><text x="22" y="102">WPS meetings</text>
    </g>
  </svg>
  <p class="abs about">The Quiet Pathfinder Course is a 4-month long transformative journey for people who feel stuck or not entirely satisfied with their work and/or life. It will be of benefit for everyone, at any stage. The Program consists of a series of four 5-hour workshops, one per month, complemented by 2-hour weekly peer support meetings. It combines mindfulness techniques, design thinking methodology and entrepreneurship frameworks to achieve the desired</p>

  <h2 class="band band-prog">The Program</h2>
  <p class="abs prog-text">Many people are not entirely satisfied with their work, but they don't know what to do about it. The Quiet Pathfinder Course offers an opportunity, a safe place, a collective journey to help you reflect, design, and (very likely) do something about it. By the end of the Program, you should have:</p>
  <ul class="abs ticks">
    <li><svg class="tick" viewBox="0 0 10 10"><path d="M1 5 L4 8 L9 1" fill="none" stroke="var(--orange)" stroke-width="2"/></svg>Increased awareness, clarity and confidence</li>
    <li><svg class="tick" viewBox="0 0 10 10"><path d="M1 5 L4 8 L9 1" fill="none" stroke="var(--blue)" stroke-width="2"/></svg>A deeper insight on what makes you happier and what you want</li>
    <li><svg class="tick" viewBox="0 0 10 10"><path d="M1 5 L4 8 L9 1" fill="none" stroke="var(--green-deep)" stroke-width="2"/></svg>A clear design integrating your intended work and life Initiated the execution of this design.</li>
  </ul>

  <h2 class="band band-why">Why</h2>
  <div class="abs walk-photo" role="img" aria-label="Faint photo of a person walking along a forest path"></div>
  <p class="abs why-head">This Program differs from existing entrepreneurial programs in many ways:</p>
  <ul class="abs why-list why-left">
    <li><svg class="tick" viewBox="0 0 10 10"><path d="M1 5 L4 8 L9 1" fill="none" stroke="var(--orange)" stroke-width="2"/></svg>It starts upstream with mindfulness and self analysis to look deeply into yourself</li>
    <li><svg class="tick" viewBox="0 0 10 10"><path d="M1 5 L4 8 L9 1" fill="none" stroke="var(--blue)" stroke-width="2"/></svg>Design and execution decisions are rooted on happiness rather than (only) financials</li>
  </ul>
  <div class="abs divider"></div>
  <ul class="abs why-list why-right">
    <li><svg class="tick" viewBox="0 0 10 10"><path d="M1 5 L4 8 L9 1" fill="none" stroke="var(--green-deep)" stroke-width="2"/></svg>The process is holistic and inclusive, aiming at designing an integrated work and life, and on building synergies between your different parts.</li>
  </ul>
  <p class="abs format">The Program format includes lectures, individual work, group sharing, guided activities, experiential exercises, video, audio, handouts and other resources.</p>

  <p class="abs band-way">THE WAY OUT IS IN</p>
  <p class="abs contact contact-left">Date: Thursday 23th, from 19:30 to 21:00<br>Venue: Lumen Coworking, C/ Olivar 42, Valmora</p>
  <p class="abs contact contact-right">Email: info@brightmeadow.io<br>Tel: +34 611 402 735 (video call and chat)</p>
</section>

</body>
</html>
```